Garlic Farm for Farm Sales/Restaurant sales

Need a professional, but appealing to agriculture world. We are selling 27 kinds of Organic Garlic from a farm in Simla,CO. I have uploaded logo and business information-we are going to need a template, because I will need to use it for four separate people.
-We are trying to appeal to Farm to table restaurants
-As well as growers/farmers

Target Market(s)

Agriculture Sales/Restaurants-Organic

Industry/Entity Type

Agriculture

Contact Information for Business Card

Want it to look more unique then your average kelto stock card- I want it to look amazing

Font styles to use
Sans Serif

Colors
0455a3
ec1f27
fbed22
ffffff

Requirements
Must have
• Just be creative
Nice to have
• Colorful
Should not have
• plain

```html
<!DOCTYPE html>
<html lang="en">
<head>
<meta charset="utf-8">
<title>Prairie Crest Garlic – Business Card</title>
<link rel="stylesheet" href="https://fonts.googleapis.com/css2?family=Open+Sans:wght@400;600;700&display=swap">
<style>
  :root {
    --navy: #0b2f5e;
    --red: #c8102e;
    --yellow: #fbed22;
    --white: #ffffff;
    --ink: #4a4f57;
    --rule: #d9dbe0;
    --backdrop: #e8e5e0;
  }
  * { margin: 0; padding: 0; box-sizing: border-box; }
  html, body {
    width: 1200px; height: 987px; overflow: hidden;
    background: var(--backdrop);
    font-family: "Open Sans", sans-serif;
  }
  .stage { position: relative; width: 1200px; height: 987px; }
  .card {
    position: absolute; width: 615px; height: 352px;
    box-shadow: 0 2px 6px rgba(0,0,0,.18);
  }
  .card--front { left: 293px; top: 130px; background: var(--white); }
  .card--back { left: 292px; top: 506px; background: var(--navy); }

  .brand {
    position: absolute; left: 70px; top: 108px; width: 220px;
    display: flex; flex-direction: column; align-items: center; gap: 16px;
  }
  .brand__dot { width: 86px; height: 86px; border-radius: 50%; background: var(--red); }
  .brand__name {
    font-weight: 700; font-size: 20px; color: var(--navy);
    white-space: nowrap; letter-spacing: .2px; line-height: 1.1;
  }
  .divider {
    position: absolute; left: 322px; top: 88px; width: 1px; height: 196px;
    background: var(--rule);
  }
  .contact { position: absolute; left: 363px; top: 92px; color: var(--ink); }
  .contact__name { font-size: 22px; font-weight: 700; color: var(--navy); line-height: 1.1; }
  .contact__role { font-size: 16px; color: var(--red); margin-top: 2px; }
  .contact__address { font-size: 15px; line-height: 22px; margin-top: 14px; }
  .contact__list { list-style: none; margin-top: 14px; font-size: 15px; line-height: 23px; }
  .contact__list li { display: flex; align-items: center; gap: 7px; }
  .contact__list svg { width: 13px; height: 13px; fill: var(--navy); flex: none; }

  .back-mark {
    position: absolute; left: 230px; top: 102px;
    width: 142px; height: 142px; border-radius: 50%;
    background: var(--red);
  }
  .social {
    position: absolute; left: 107px; top: 292px; width: 369px; height: 24px;
  }
  .social svg { width: 100%; height: 100%; display: block; }
</style>
</head>
<body>
<main class="stage">
  <section class="card card--front">
    <div class="brand">
      <span class="brand__dot"></span>
      <span class="brand__name">Prairie Crest Garlic</span>
    </div>
    <div class="divider"></div>
    <div class="contact">
      <h1 class="contact__name">DALE PERRIN</h1>
      <p class="contact__role">CEO/FOUNDER</p>
      <p class="contact__address">P.O. Box 48 Harlow<br>CO&nbsp; 80712</p>
      <ul class="contact__list">
        <li><svg viewBox="0 0 16 16"><path d="M3.6 1l2.6 3-1.5 1.8c.9 2 2.5 3.6 4.5 4.5L11 8.8l3 2.6-1.2 2.8C7 14.5 1.5 9 1.8 3.2z"/></svg>555-014-2736</li>
        <li><svg viewBox="0 0 16 16"><path d="M1 3h14v10H1zM2.5 4.5v.4L8 9l5.5-4.1v-.4zM2.5 6.7v4.8h11V6.7L8 10.8z"/></svg>Nell@PCGarlic.com</li>
        <li><svg viewBox="0 0 16 16"><circle cx="8" cy="8" r="7"/></svg>www.PCGarlic.com</li>
      </ul>
    </div>
  </section>

  <section class="card card--back">
    <span class="back-mark"></span>
    <div class="social">
      <svg viewBox="0 0 369 24" fill="none" stroke="#ffffff" stroke-width="1">
        <line x1="0" y1="12" x2="130" y2="12" opacity=".6"/>
        <line x1="239" y1="12" x2="369" y2="12" opacity=".6"/>
        <circle cx="144" cy="12" r="10.5"/>
        <circle cx="170" cy="12" r="10.5"/>
        <circle cx="197" cy="12" r="10.5"/>
        <circle cx="224" cy="12" r="10.5"/>
      </svg>
    </div>
  </section>
</main>
</body>
</html>
```